Brell Stone Company Business Cards

Front and Back Business Card - logo and text setup - cool design. I need workable photoshop or illustrator files so I can setup each employee card with design that is created
Updates

Hi everyone, thank you for the great entries. Please no more white and blue cards - there are so many already - black and silver only now please. thanks!

Target Market(s)

Construction Industry - Facility Managers

Industry/Entity Type

Construction

Contact Information for Business Card

I really like contemporary simplistic looks - clean neat....not opposed to seeing some black backrounds

Requirements
Must have
• Logo/website address with design on front only - www.brellstone-example.com (logo attached)
• Back:
• Name/Title/Company Address/Phone/email address
Nice to have
• Cool design
Should not have
• Nothing gimmicky like Fire or Water - since we are a Fire Protection company - it has all been done

```html
<!DOCTYPE html>
<html lang="en">
<head>
<meta charset="utf-8">
<title>Brell Stone Company Business Cards</title>
<link rel="stylesheet" href="https://fonts.googleapis.com/css2?family=Open+Sans:wght@400;600;700;800&display=swap">
<style>
  :root {
    --backdrop: #2a2a2c;
    --card: #1d1d1f;
    --card-edge: #2c2c2f;
    --silver: #b9babd;
    --ink: #f2f2f2;
    --accent: #e8452f;
  }
  * { margin: 0; padding: 0; box-sizing: border-box; }
  html, body {
    width: 1200px;
    height: 874px;
    overflow: hidden;
    background: var(--backdrop);
    font-family: "Open Sans", Arial, sans-serif;
  }
  .canvas {
    position: relative;
    width: 1200px;
    height: 874px;
  }
  .card {
    position: absolute;
    width: 560px;
    height: 320px;
    left: 320px;
    background: var(--card);
    border: 1px solid var(--card-edge);
    border-radius: 18px;
  }
  .card--front { top: 92px; }
  .card--back { top: 462px; }

  .brand-name {
    position: absolute;
    top: 50%;
    left: 50%;
    transform: translate(-50%, -50%);
    font-weight: 800;
    font-size: 64px;
    letter-spacing: -1px;
    color: var(--silver);
    white-space: nowrap;
  }

  .contact {
    position: absolute;
    left: 52px;
    top: 58px;
    color: var(--ink);
    font-size: 14px;
    line-height: 1.32;
  }
  .contact__name {
    font-weight: 600;
    font-size: 21px;
    color: var(--accent);
    text-transform: uppercase;
    line-height: 1.15;
  }
  .contact__title {
    font-size: 15px;
    margin-bottom: 12px;
  }
  .contact__address { margin-bottom: 12px; }
  .contact__label {
    color: var(--accent);
    font-weight: 700;
  }
  .contact__web {
    margin-top: 10px;
    color: var(--accent);
    font-size: 15px;
  }
</style>
</head>
<body>
  <main class="canvas">
    <section class="card card--front" aria-label="Card front">
      <div class="brand-name">Brell Stone</div>
    </section>

    <section class="card card--back" aria-label="Card back">
      <div class="contact">
        <p class="contact__name">Dana Whitlock</p>
        <p class="contact__title">CEO/Founder</p>
        <p class="contact__address">48 Harbor Park Road<br>Millbrook, NY 10000</p>
        <p><span class="contact__label">P.</span> (555) 014-2200</p>
        <p><span class="contact__label">F.</span> (555) 014-2201</p>
        <p><span class="contact__label">E.</span> info@brellstone-example.com</p>
        <p class="contact__web">www.brellstone-example.com</p>
      </div>
    </section>
  </main>
</body>
</html>
```